Coastal Learner Bureau business cards

Australian company about to start offering its services. We recruit international students to come to study English, vocational education and postgraduate courses in Australia. We help them find the institution and select the right city they want to come to Australia. We are a young, online oriented and supportive agency. Our clients are between 18 and 35 years old, mainly University students, young professionals or people with work experience. We provide much more information that any other agency offer. We administrate a Facebook group with more than 11.000 members that daily ask questions about general information when coming to Australia, while they are here and even after they leave the country

Target Market(s)

International students from South America, Central America and Europe

Industry/Entity Type

Student

Contact Information for Business Card

Tomas Bilbrea
Managing Director
tomas@kelvarin.com.au
www.kelvoria.com.au
+61 491058264
Melbourne, Australia

Font styles to use
Serif
Sans Serif

Colors

Designer to choose colors to be used in the design.

Requirements
Must have
• Horizontal design
• Standard business card size and shape. If font uses green or yellow colours, they will have to match the ones from the logo
Nice to have
• UPDATE: Use the contents of the green image to design one of the card sides. Use our logo in the background of that side as watermark.
• Passport image, or immigration stamps. A picture of the Yarra River (from Melbourne) would be cool as well.
Should not have
• Non-standard business card size and shape
• Not black as the background colour of any sides as we are not a VIP agency or a hight class service. We are orientes to young people and they like colours, pictures, something attractive.
• Vertical design
• NO YELLOW or BLACK AS THE BACKGROUND COLOUR OF ANY SIDE OF THE BIZ CARD

```html
<!DOCTYPE html>
<html lang="en">
<head>
<meta charset="utf-8">
<title>Coastal Learner Bureau business cards</title>
<link href="https://fonts.googleapis.com/css2?family=Jost:wght@400;500;600&display=swap" rel="stylesheet">
<style>
  :root {
    --backdrop: #2b2b2d;
    --card: #17324a;
    --card-edge: #1d3c58;
    --white: #f4f4f4;
    --gold: #e7bd1e;
    --green: #34a26a;
  }
  * { margin: 0; padding: 0; box-sizing: border-box; }
  html, body { width: 1200px; height: 900px; overflow: hidden; }
  body {
    background: var(--backdrop);
    font-family: "Jost", sans-serif;
    color: var(--white);
    display: flex;
    flex-direction: column;
    align-items: center;
    justify-content: center;
    gap: 40px;
  }
  .card {
    width: 700px;
    height: 400px;
    background: linear-gradient(160deg, var(--card-edge), var(--card));
    position: relative;
    box-shadow: 0 10px 30px rgba(0,0,0,.45);
  }
  .card--front {
    display: flex;
    flex-direction: column;
    align-items: center;
    justify-content: center;
  }
  .front-brand {
    font-size: 40px;
    font-weight: 500;
    color: var(--white);
    letter-spacing: .5px;
    margin-top: -20px;
  }
  .front-tagline {
    position: absolute;
    bottom: 48px;
    left: 0; right: 0;
    text-align: center;
    font-size: 15px;
    letter-spacing: 1.5px;
    font-weight: 500;
  }
  .card--back {
    display: flex;
    align-items: center;
    padding: 0 36px 0 44px;
  }
  .back-brand {
    width: 250px;
    display: flex;
    align-items: center;
    gap: 14px;
  }
  .brand-dot {
    width: 22px; height: 22px;
    border-radius: 50%;
    background: var(--gold);
    flex: none;
  }
  .brand-name {
    font-size: 32px;
    font-weight: 500;
    line-height: 1.1;
    color: var(--green);
  }
  .divider {
    width: 2px;
    height: 180px;
    background: var(--green);
    margin: 0 30px 0 22px;
    flex: none;
  }
  .details { flex: 1; min-width: 0; }
  .person-name {
    font-size: 28px;
    font-weight: 600;
    color: var(--gold);
    letter-spacing: 2px;
    text-transform: uppercase;
    line-height: 1;
    white-space: nowrap;
  }
  .person-role {
    font-size: 20px;
    letter-spacing: 1px;
    margin: 6px 0 18px;
  }
  .contact-list { list-style: none; }
  .contact-item {
    display: flex;
    align-items: center;
    gap: 14px;
    font-size: 18px;
    letter-spacing: 1.2px;
    line-height: 1.6;
    white-space: nowrap;
  }
  .contact-icon { width: 14px; height: 14px; flex: none; }
  .accent { color: var(--gold); }
</style>
</head>
<body>
  <section class="card card--front">
    <div class="front-brand">Coastal Learner Bureau</div>
    <p class="front-tagline">Hacemos más por ti!</p>
  </section>

  <section class="card card--back">
    <div class="back-brand">
      <span class="brand-dot"></span>
      <span class="brand-name">Coastal Learner Bureau</span>
    </div>
    <div class="divider"></div>
    <div class="details">
      <h1 class="person-name">Tomas Bilbrea</h1>
      <p class="person-role">Managing Director</p>
      <ul class="contact-list">
        <li class="contact-item">
          <svg class="contact-icon" viewBox="0 0 14 14"><rect x="3.5" y="1" width="7" height="12" rx="1.2" fill="none" stroke="#e7bd1e" stroke-width="1.6"/></svg>
          +61 491058264
        </li>
        <li class="contact-item">
          <svg class="contact-icon" viewBox="0 0 14 14"><rect x="1" y="3" width="12" height="8.5" fill="#e7bd1e"/><path d="M1 3.5 7 8l6-4.5" fill="none" stroke="#17324a" stroke-width="1.2"/></svg>
          tomas@kelvarin.com.au
        </li>
        <li class="contact-item">
          <svg class="contact-icon" viewBox="0 0 14 14"><circle cx="6" cy="6" r="4" fill="none" stroke="#e7bd1e" stroke-width="2"/><path d="M9 9l4 4" stroke="#e7bd1e" stroke-width="2.2" stroke-linecap="round"/></svg>
          <span>www.<span class="accent">kelvoria.com</span>.au</span>
        </li>
        <li class="contact-item">
          <svg class="contact-icon" viewBox="0 0 14 14"><path d="M7 13.5S2 8.3 2 5.2a5 5 0 0 1 10 0C12 8.3 7 13.5 7 13.5z" fill="#e7bd1e"/><circle cx="7" cy="5.2" r="1.8" fill="#17324a"/></svg>
          Melbourne, Australia
        </li>
      </ul>
    </div>
  </section>
</body>
</html>
```